Alloy wheel repair business needs a website

Install logo previously purchased from makerhive, toolbar with dropdowns. services, gallery, clients , contact ect
Maybe mission statment

Target Market(s)

vehicle owners, auto dealers,insurance companies,

Industry/Entity Type

Alloy Wheel Repair

Coding

Coded - Design and coding required

Number of Pages Required

4 page

Font styles to use
Sans Serif

Colors
0054AA
0677BA
7BADD7
CADEEF
E8F1F8

```html
<!DOCTYPE html>
<html lang="en">
<head>
<meta charset="utf-8">
<title>Rimwell Wheel Studio</title>
<link href="https://fonts.googleapis.com/css2?family=IBM+Plex+Sans:wght@400;500;600;700&family=Michroma&display=swap" rel="stylesheet">
<style>
:root{
  --blue:#3f87cc;
  --blue-deep:#0054AA;
  --blue-mid:#0677BA;
  --blue-soft:#7BADD7;
  --blue-pale:#CADEEF;
  --blue-wash:#E8F1F8;
  --ink:#1d1d1f;
  --text:#555a60;
  --footer:#231f20;
  --white:#fff;
}
*{margin:0;padding:0;box-sizing:border-box}
html,body{width:1200px;height:3862px;overflow:hidden}
body{font-family:"IBM Plex Sans",sans-serif;color:var(--text);background:var(--white);position:relative}
.abs{position:absolute}
.display{font-family:"Michroma",sans-serif;letter-spacing:1px}
.accent{color:var(--blue)}
.photo{position:absolute}

/* header */
.header{position:absolute;top:0;left:0;width:1200px;height:125px;border-top:4px solid var(--blue);background:var(--white)}
.social{display:flex;gap:7px;position:absolute}
.social span{width:30px;height:30px;border:1.5px solid #333;border-radius:50%;display:block}
.social.dark span{border-color:#fff}
.phone-tab{position:absolute;left:775px;top:0;width:310px;height:44px;background:var(--blue);color:#fff;font-weight:600;font-size:19px;display:flex;align-items:center;justify-content:center;gap:10px;clip-path:polygon(0 0,100% 0,88% 100%,8% 100%)}
.nav a{position:absolute;top:78px;font-size:15px;font-weight:500;color:#222;text-decoration:none;letter-spacing:.3px}
.nav a.active{color:var(--blue)}
.brand{position:absolute;left:475px;top:36px;width:250px;display:flex;align-items:center;justify-content:center;gap:10px;font-weight:700;font-size:30px;color:var(--blue);letter-spacing:1px}
.brand i{width:16px;height:16px;background:var(--blue);border-radius:50%;display:block}

/* hero */
.hero{position:absolute;top:125px;left:0;width:1200px;height:627px;background:linear-gradient(100deg,#1d2838 0%,#2b4466 45%,#3e6a9c 70%,#5a8cc4 100%)}
.hero h1{position:absolute;left:112px;top:180px;color:#fff;font-size:42px;line-height:56px;font-weight:400}
.hero p{position:absolute;left:112px;top:293px;width:500px;color:#fff;font-size:18px;line-height:30px;font-weight:500}
.btn{position:absolute;background:var(--blue);color:#fff;font-size:15px;font-weight:600;display:flex;align-items:center;justify-content:center;letter-spacing:.3px}
.btn::after{content:"";position:absolute;left:8px;top:8px;right:-8px;bottom:-8px;border:1.5px solid #222}
.hero .btn::after{border-color:#fff}
.dots{position:absolute;left:563px;top:587px;display:flex;gap:11px}
.dots span{width:10px;height:10px;border:1.5px solid #fff;border-radius:50%}
.dots span.on{background:#fff}

/* about */
.framed{position:absolute;border:6px solid #fff;box-shadow:0 2px 10px rgba(0,0,0,.15)}
h2{font-family:"Michroma",sans-serif;font-weight:400;color:var(--ink);letter-spacing:1px}
.copy{font-size:14.5px;line-height:26px;text-align:justify}
.copy p+p{margin-top:17px}

/* services */
.services{position:absolute;top:1500px;left:0;width:1200px;height:670px;background:var(--blue-wash)}
.card{position:absolute;top:238px;width:283px;height:344px}
.card .label{position:absolute;left:0;right:0;bottom:30px;text-align:center;color:#fff;font-weight:700;font-size:16px;letter-spacing:.3px}
.card.active{background:linear-gradient(180deg,rgba(63,135,204,.93),rgba(63,135,204,.96)),#3f87cc;color:#fff;text-align:center}

/* gallery */
.gallery{position:absolute;top:2895px;left:0;width:1200px;height:600px;background:linear-gradient(120deg,#3f82c6,#4d8fd0 50%,#3b7cc0)}
.tile{position:absolute;border:3px solid #fff}

/* footer */
.footer{position:absolute;top:3495px;left:0;width:1200px;height:367px;background:var(--footer);color:#fff}
.footer h4{font-family:"Michroma",sans-serif;font-weight:400;font-size:15px;letter-spacing:1px;position:absolute;top:65px}
.flist{position:absolute;top:108px;font-size:14px;line-height:38px;color:#e8e8e8}
.contact-row{position:absolute;left:417px;display:flex;gap:20px;font-size:14px;line-height:23px;color:#e8e8e8}
.contact-row .ic{width:36px;height:36px;border-radius:50%;background:#fff;display:flex;align-items:center;justify-content:center;flex:none}
</style>
</head>
<body>

<header class="header">
  <div class="social" style="left:165px;top:20px"><span></span><span></span><span></span></div>
  <div class="phone-tab">
    <svg width="16" height="16" viewBox="0 0 24 24"><path fill="#fff" d="M6.6 10.8a15.1 15.1 0 0 0 6.6 6.6l2.2-2.2a1 1 0 0 1 1-.25 11.4 11.4 0 0 0 3.6.57 1 1 0 0 1 1 1V20a1 1 0 0 1-1 1A17 17 0 0 1 3 4a1 1 0 0 1 1-1h3.5a1 1 0 0 1 1 1c0 1.25.2 2.45.57 3.57a1 1 0 0 1-.25 1z"/></svg>
    555 - 014 - 2288
  </div>
  <nav class="nav">
    <a class="active" href="#" style="left:110px">HOME</a>
    <a href="#" style="left:183px">SERVICES</a>
    <a href="#" style="left:287px">GALLERY</a>
    <a href="#" style="left:862px">CLIENTS</a>
    <a href="#" style="left:955px">CONTACT</a>
    <a href="#" style="left:1046px">|</a>
    <svg class="abs" style="left:1073px;top:80px" width="15" height="15" viewBox="0 0 24 24"><circle cx="10" cy="10" r="7" fill="none" stroke="#222" stroke-width="3"/><path d="M15 15l6 6" stroke="#222" stroke-width="3"/></svg>
  </nav>
  <div class="brand"><i></i>RIMWELL</div>
</header>

<section class="hero" role="img" aria-label="Technician in gloves mounting an alloy wheel with a tyre in a workshop, blue tint">
  <h1 class="display"><span class="accent">RIMWELL</span><br>WHEEL STUDIO</h1>
  <p>Lorem ipsum dolor sit amet, consectetur adipiscing elit se do eiusmod tempor incidiea.</p>
  <div class="btn" style="left:117px;top:382px;width:145px;height:52px">GET STARTED</div>
  <div class="dots"><span></span><span class="on"></span><span></span><span></span></div>
</section>

<section class="about">
  <svg class="abs" style="left:216px;top:1120px" width="226" height="268"><path d="M1 0V266H224V240" fill="none" stroke="var(--blue)" stroke-width="2.5"/><path d="M343 0" /></svg>
  <div class="abs" style="left:343px;top:1123px;width:30px;height:2px;background:var(--blue)"></div>
  <div class="framed" style="left:112px;top:929px;width:232px;height:352px"><div class="photo" role="img" aria-label="Car on a lift with alloy wheel in a garage" style="inset:0;background:linear-gradient(160deg,#3a4250,#1e2b3c 60%,#2c5a8e)"></div></div>
  <div class="framed" style="left:366px;top:871px;width:236px;height:180px"><div class="photo" role="img" aria-label="Mechanic working on alloy wheels with red gloves" style="inset:0;background:linear-gradient(150deg,#4a4f56,#7c8089 50%,#2f3a48)"></div></div>
  <div class="framed" style="left:366px;top:1075px;width:236px;height:280px"><div class="photo" role="img" aria-label="Technician with impact wrench on a car wheel" style="inset:0;background:linear-gradient(160deg,#3d4a5c,#2c5d97 55%,#6b6f75)"></div></div>

  <h2 class="abs" style="left:667px;top:928px;font-size:36px">ABOUT <span class="accent">US</span></h2>
  <div class="copy abs" style="left:667px;top:998px;width:422px">
    <p>Lorem ipsum dolor sit amet, consectetur adipiscing elit, sed do eiusmod tempor incididunt ut labore et dolore magna aliqua. Ut enim ad minim veniam, quis nostrud exercitation ullamco laboris nisi ut aliquip ex ea commodo consequat duis aute irure dolor in reprehenderit.</p>
    <p>Lorem ipsum dolor sit amet, consectetur adipiscing elit, sed do eiusmod tempor incididunt ut labore et dolore magna aliqua ut enim ad minim.</p>
  </div>
  <div class="btn" style="left:667px;top:1260px;width:151px;height:56px">LEARN MORE</div>
</section>

<section class="services">
  <h2 class="abs" style="left:0;width:1200px;text-align:center;top:85px;font-size:36px">OUR <span class="accent">SERVICES</span></h2>
  <p class="abs" style="left:130px;width:940px;text-align:center;top:148px;font-size:15.5px;line-height:26px">Lorem ipsum dolor sit amet, consectetur adipiscing elit, sed do eiusmod tempor incididunt ut labore et dolore magna aliqua ut nostrud exercitation ullamco laboris nisi ut aliquip .</p>
  <div class="card" style="left:13px" role="img" aria-label="Mechanic straightening a wheel"><div class="photo" style="inset:0;background:linear-gradient(170deg,#5a5650,#2d2a28 60%,#3f4d60)"></div><div class="label">WHEEL STRAIGHTENING</div></div>
  <div class="card" style="left:310px" role="img" aria-label="Worker handling a tyre in a workshop"><div class="photo" style="inset:0;background:linear-gradient(170deg,#9a6a45,#4b4640 55%,#2e2c2b)"></div><div class="label">WHEEL REMANUFACTURING</div></div>
  <div class="card active" style="left:607px">
    <svg style="margin-top:38px" width="60" height="60" viewBox="0 0 60 60"><circle cx="30" cy="30" r="27" fill="none" stroke="#fff" stroke-width="4"/><circle cx="30" cy="30" r="6" fill="none" stroke="#fff" stroke-width="3"/><g fill="none" stroke="#fff" stroke-width="3"><circle cx="30" cy="16" r="6"/><circle cx="43" cy="26" r="6"/><circle cx="38" cy="41" r="6"/><circle cx="22" cy="41" r="6"/><circle cx="17" cy="26" r="6"/></g></svg>
    <div style="font-weight:700;font-size:16px;margin-top:10px;letter-spacing:.3px">WHEEL REFINISHING</div>
    <div style="width:6px;height:6px;border-radius:50%;background:#fff;margin:8px auto 0"></div>
    <p style="font-size:14.5px;line-height:26px;font-weight:500;margin:12px 24px 0">Lorem ipsum dolor sit amet, con sectetur adipiscing elit, sed do eiusmod tempor incididunt ut labore sed dolorea.</p>
    <div style="font-size:14px;font-weight:700;text-decoration:underline;margin-top:14px">LEARN MORE</div>
  </div>
  <div class="card" style="left:904px" role="img" aria-label="Gloved hands fitting a tyre on an alloy rim"><div class="photo" style="inset:0;background:linear-gradient(170deg,#5d5e60,#2a2b2d 55%,#4a4c50)"></div><div class="label">WHEEL CUSTOM COLORING</div></div>
</section>

<section class="mission">
  <h2 class="abs" style="left:112px;top:2302px;font-size:30px">OUR <span class="accent">MISSION</span></h2>
  <div class="copy abs" style="left:112px;top:2365px;width:422px">
    <p>Lorem ipsum dolor sit amet, consectetur adipiscing elit, sed do eiusmod tempor incididunt ut labore et dolore magna aliqua. Ut enim ad minim veniam, quis nostrud exercitation ullamco laboris nisi ut aliquip ex ea commodo consequat duis aute irure dolor in reprehenderit.</p>
    <p>Lorem ipsum dolor sit amet, consectetur adipiscing elit, sed do eiusmod tempor incididunt ut labore et dolore magna aliqua ut enim ad minim.</p>
  </div>
  <div class="btn" style="left:112px;top:2625px;width:151px;height:54px">CONTACT US</div>
  <div class="photo" role="img" aria-label="Gloved hand using an impact wrench on a car's alloy wheel" style="left:591px;top:2292px;width:497px;height:410px;background:linear-gradient(150deg,#1f2e4e,#3b4a60 45%,#9aa3ad 75%,#d8dadc)"></div>
  <div class="abs" style="left:591px;top:2645px;width:386px;height:118px;background:#fff;box-shadow:0 4px 14px rgba(0,0,0,.15)">
    <div class="abs" style="left:35px;top:30px;width:62px;height:62px;border-radius:50%;border:2px solid #222;display:flex;align-items:center;justify-content:center">
      <div style="width:48px;height:48px;border-radius:50%;background:var(--blue);display:flex;align-items:center;justify-content:center"><svg width="20" height="20" viewBox="0 0 24 24"><path fill="#fff" d="M6.6 10.8a15.1 15.1 0 0 0 6.6 6.6l2.2-2.2a1 1 0 0 1 1-.25 11.4 11.4 0 0 0 3.6.57 1 1 0 0 1 1 1V20a1 1 0 0 1-1 1A17 17 0 0 1 3 4a1 1 0 0 1 1-1h3.5a1 1 0 0 1 1 1c0 1.25.2 2.45.57 3.57a1 1 0 0 1-.25 1z"/></svg></div>
    </div>
    <div class="abs" style="left:120px;top:33px;font-size:12px;font-weight:700;color:#222">CALL US TODAY!</div>
    <div class="abs" style="left:120px;top:50px;font-size:30px;font-weight:700;color:var(--blue)">555 - 014 - 2288</div>
  </div>
</section>

<section class="gallery">
  <h2 class="abs" style="left:0;width:1200px;text-align:center;top:63px;font-size:34px;color:#fff">GALLERY</h2>
  <div class="tile" role="img" aria-label="Hand holding a new tyre on an alloy wheel" style="left:112px;top:150px;width:230px;height:178px;background:linear-gradient(160deg,#a9b3bd,#3d4044 60%,#6a7079)"></div>
  <div class="tile" role="img" aria-label="Stacked dark alloy wheels" style="left:360px;top:150px;width:231px;height:178px;background:linear-gradient(160deg,#d0d3d6,#5a5c60 50%,#2a2b2e)"></div>
  <div class="tile" role="img" aria-label="Mechanic with a tyre in a workshop" style="left:608px;top:150px;width:231px;height:178px;background:linear-gradient(160deg,#7c5a3f,#3a3a3c 55%,#7e8288)"></div>
  <div class="tile" role="img" aria-label="Red-gloved hands working on a wheel" style="left:857px;top:150px;width:231px;height:378px;background:linear-gradient(170deg,#55585d,#8e3333 45%,#2c2d30)"></div>
  <div class="tile" role="img" aria-label="Technician servicing a wheel in warm light" style="left:112px;top:350px;width:479px;height:178px;background:linear-gradient(100deg,#3b4c66,#8a5a58 45%,#f29a5a 62%,#3a4256)"></div>
  <div class="tile" role="img" aria-label="Tyre being fitted on an alloy rim" style="left:608px;top:350px;width:231px;height:178px;background:linear-gradient(160deg,#3c4656,#222326 55%,#6e747c)"></div>
</section>

<footer class="footer">
  <div class="brand" style="left:112px;top:150px;width:auto;color:#fff;font-size:32px;justify-content:flex-start"><i style="background:#fff"></i>RIMWELL</div>

  <h4 style="left:417px">CONTACT US</h4>
  <div class="contact-row" style="top:105px"><span class="ic"><svg width="14" height="16" viewBox="0 0 24 28"><path fill="var(--blue)" d="M12 0a10 10 0 0 0-10 10c0 7 10 18 10 18s10-11 10-18A10 10 0 0 0 12 0zm0 14a4 4 0 1 1 0-8 4 4 0 0 1 0 8z"/></svg></span><div>42 FOUNDRY LANE<br>BROOKVALE PA 10420</div></div>
  <div class="contact-row" style="top:165px"><span class="ic"><svg width="15" height="15" viewBox="0 0 24 24"><path fill="var(--blue)" d="M6.6 10.8a15.1 15.1 0 0 0 6.6 6.6l2.2-2.2a1 1 0 0 1 1-.25 11.4 11.4 0 0 0 3.6.57 1 1 0 0 1 1 1V20a1 1 0 0 1-1 1A17 17 0 0 1 3 4a1 1 0 0 1 1-1h3.5a1 1 0 0 1 1 1c0 1.25.2 2.45.57 3.57a1 1 0 0 1-.25 1z"/></svg></span><div>CALL US:<br>555 - 014 - 2288</div></div>
  <div class="contact-row" style="top:225px"><span class="ic"><svg width="16" height="12" viewBox="0 0 24 18"><rect width="24" height="18" rx="2" fill="var(--blue)"/><path d="M1 2l11 8 11-8" fill="none" stroke="#fff" stroke-width="2"/></svg></span><div>EMAIL US:<br>HELLO@RIMWELLWHEELS.EXAMPLE</div></div>

  <h4 style="left:749px">LINKS</h4>
  <div class="flist" style="left:749px">HOME<br>SERVICES<br>GALLERY<br>CLIENTS<br>CONTACT</div>

  <h4 style="left:900px">SERVICES</h4>
  <div class="flist" style="left:900px">WHEEL STRAIGHTENING<br>WHEEL REMANUFACTURING<br>WHEEL REFINISHING<br>WHEEL CUSTOM COLORING</div>

  <div class="abs" style="left:112px;top:305px;width:976px;height:1px;background:#4a4647"></div>
  <div class="abs" style="left:0;width:1200px;text-align:center;top:327px;font-size:13px">© 2023 RIMWELL WHEEL STUDIO - ALL RIGHTS RESERVED.</div>
  <div class="social dark" style="left:977px;top:318px"><span></span><span></span><span></span></div>
  <div class="abs" style="left:1132px;top:330px;font-size:9px">C45</div>
</footer>

</body>
</html>
```